Business card for Luxury Portable Restroom Trailer company

We are a Luxury Portable Restroom Trailer Company Called FALCRIDGE HIRES. Based in Orange County California. We provide portable restroom trailers for events, such as, Weddings, Concerts, Charity events, Sporting events, Tournaments, Corporate events, ect. We rent and Sell the Luxury restrooms. Our colors are white, grey, and Orange. As you will see in the logo we uploaded.
There are 2 people in the company so the names and titles will change for the 3 people but card will remain the same. Here is the information for each Person: Dwight Penner CFO 555 318-0476
next Person: Leon Marchetti VP 555 318-0476
Next Person: Owen Marchetti CEO 555 318-0476
Information to include on the card: Luxury Restroom Trailers Rental and Sales. Weddings, Concerts, Charity, Sporting and Corp. Events.

```html
<!DOCTYPE html>
<html lang="en">
<head>
<meta charset="utf-8">
<title>FALCRIDGE HIRES – Business Card</title>
<link href="https://fonts.googleapis.com/css2?family=Montserrat:wght@400;500;600;700;800&display=swap" rel="stylesheet">
<style>
  :root {
    --orange: #f06a25;
    --white: #ffffff;
    --ink: #1f1f22;
    --grey: #4a4a4f;
    --stage: #e6e6e8;
  }
  * { box-sizing: border-box; margin: 0; padding: 0; }
  html, body {
    width: 1200px; height: 900px; overflow: hidden;
    background: var(--stage);
    font-family: "Montserrat", sans-serif;
  }
  .canvas { position: relative; width: 1200px; height: 900px; }
  .card {
    position: absolute; left: 250px;
    width: 700px; height: 400px;
    border-radius: 22px; overflow: hidden;
    box-shadow: 0 6px 18px rgba(0,0,0,0.15);
  }
  .card--front { top: 36px; background: var(--orange); }
  .card--back { top: 464px; background: var(--white); }

  .front-content {
    position: absolute; inset: 0;
    display: flex; flex-direction: column; align-items: center; justify-content: center;
    color: var(--white); text-align: center;
  }
  .front-name {
    font-weight: 800; font-size: 54px; letter-spacing: 3px; line-height: 1.1;
  }
  .front-rule {
    width: 120px; height: 3px; background: var(--white); margin: 22px 0 18px;
  }
  .front-tagline {
    font-weight: 700; font-size: 18px; letter-spacing: 1.5px; text-transform: uppercase;
  }
  .front-events {
    font-weight: 500; font-size: 15px; margin-top: 8px; letter-spacing: 0.3px;
  }

  .back-name {
    position: absolute; left: 48px; top: 50px;
    color: var(--orange); font-weight: 800; font-size: 24px; letter-spacing: 1.5px;
  }
  .person { position: absolute; left: 48px; top: 138px; }
  .person__name { color: var(--orange); font-weight: 700; font-size: 28px; }
  .person__title { color: var(--ink); font-weight: 500; font-size: 15px; margin-top: 2px; }
  .address {
    position: absolute; left: 48px; top: 218px;
    color: var(--ink); font-size: 14px; line-height: 1.35;
  }
  .contacts {
    position: absolute; left: 48px; top: 272px;
    list-style: none; color: var(--ink); font-size: 14px;
  }
  .contacts li { display: flex; align-items: center; gap: 10px; height: 23px; }
  .contacts svg { width: 14px; height: 14px; fill: var(--orange); flex: none; }

  .brand-disc {
    position: absolute; right: -70px; top: -40px;
    width: 380px; height: 380px;
  }
</style>
</head>
<body>
<main class="canvas">
  <section class="card card--front" aria-label="Card front">
    <div class="front-content">
      <div class="front-name">FALCRIDGE HIRES</div>
      <div class="front-rule"></div>
      <div class="front-tagline">Luxury Restroom Trailers Rental and Sales</div>
      <div class="front-events">Weddings, Concerts, Charity, Sporting and Corp. Events</div>
    </div>
  </section>

  <section class="card card--back" aria-label="Card back">
    <svg class="brand-disc" viewBox="0 0 380 380" aria-hidden="true">
      <circle cx="190" cy="190" r="180" fill="none" stroke="var(--orange)" stroke-width="16"/>
    </svg>

    <div class="back-name">FALCRIDGE HIRES</div>

    <div class="person">
      <div class="person__name">Owen Marchetti</div>
      <div class="person__title">CEO</div>
    </div>

    <div class="address">
      418 Harbor View Ave, #112<br>
      Tustin, CA 92780
    </div>

    <ul class="contacts">
      <li>
        <svg viewBox="0 0 16 16"><path d="M3 1.5l3 .5 1 3.5-2 1.5a9 9 0 0 0 4 4l1.5-2 3.5 1 .5 3-2 1.5C7 14 2 9 1.5 3.5z"/></svg>
        555 318-0476
      </li>
      <li>
        <svg viewBox="0 0 16 16"><path d="M4.5 1h7a1 1 0 0 1 1 1v12a1 1 0 0 1-1 1h-7a1 1 0 0 1-1-1V2a1 1 0 0 1 1-1zm1 2v9h5V3zM8 12.6a.8.8 0 1 0 0 1.6.8.8 0 0 0 0-1.6z"/></svg>
        555 318-0476
      </li>
      <li>
        <svg viewBox="0 0 16 16"><path d="M1 3h14v10H1zm1.5 1.5v.3L8 8.8l5.5-4v-.3zm0 2.2v4.8h11V6.7L8 10.6z"/></svg>
        info@falcridgehires.com
      </li>
      <li>
        <svg viewBox="0 0 16 16"><path d="M8 1a7 7 0 1 0 0 14A7 7 0 0 0 8 1zm0 1.5c.9 0 1.9 1.6 2.2 4.3H5.8C6.1 4.1 7.1 2.5 8 2.5zM2.6 8.2h1.8c.1 2 .6 3.7 1.3 4.8a5.5 5.5 0 0 1-3.1-4.8zm0-1.4a5.5 5.5 0 0 1 3.1-3.8c-.7 1-1.1 2.300-1.3 3.8zm5.4 6.7c-.9 0-1.9-1.9-2.2-5.3h4.4c-.3 3.4-1.3 5.3-2.2 5.3zm2.3-.5c.7-1.1 1.2-2.8 1.3-4.8h1.8a5.5 5.5 0 0 1-3.1 4.8zm1.3-6.2c-.2-1.5-.6-2.8-1.3-3.8a5.5 5.5 0 0 1 3.1 3.8z"/></svg>
        www.falcridgehires.com
      </li>
    </ul>
  </section>
</main>
</body>
</html>
```